Chimney Service company needs new business card design

We need a updated business card with our new logo added. We provide a full range of chimney services throughout Vermont and New Hampshire. The business card will be one sided and color. Attached is our current business card another document showing all the information we would like on the card.
We dont like a lot of flashy colors.... here is a link to our website to get an idea of our branding www.flueguardianvt.example

Target Market(s)

homeowners

Industry/Entity Type

Business

Contact Information for Business Card

See attached sheet for content.

Font styles to use
Serif
Sans Serif

Requirements
Must have
• all information provided on separate sheet
Should not have
• Additional information that may clogg up design

```html
<!DOCTYPE html>
<html lang="en">
<head>
<meta charset="utf-8">
<title>Flue Guardian – Business Card</title>
<link rel="stylesheet" href="https://fonts.googleapis.com/css2?family=Bebas+Neue&family=Roboto:wght@400&display=swap">
<style>
  :root {
    --page-bg: #2b2b2b;
    --card-bg: #f4f4f4;
    --ink-dark: #333333;
    --ink-body: #555555;
    --accent-red: #a50000;
    --rule-grey: #6a6a6a;
    --on-accent: #ffffff;
  }
  * { margin: 0; padding: 0; box-sizing: border-box; }
  html, body {
    width: 1200px; height: 871px; overflow: hidden;
    background: var(--page-bg);
  }
  .business-card {
    position: absolute; left: 100px; top: 150px;
    width: 1000px; height: 571px;
    background: var(--card-bg);
    font-family: "Roboto", Arial, sans-serif;
  }
  .brand {
    position: absolute; left: 40px; top: 130px; width: 440px;
    display: flex; flex-direction: column; align-items: center;
  }
  .brand-mark {
    width: 140px; height: 140px;
    background: var(--ink-dark);
  }
  .brand-name {
    margin-top: 36px;
    font-size: 42px; font-weight: 400; letter-spacing: 3px;
    color: var(--ink-dark); white-space: nowrap;
  }
  .service-info {
    position: absolute; left: 519px; top: 140px;
  }
  .service-headlines {
    font-family: "Bebas Neue", Impact, sans-serif;
    font-size: 30px; line-height: 32px; color: var(--ink-dark);
  }
  .service-list {
    list-style: none; margin-top: 12px;
    font-size: 23px; line-height: 30px; color: var(--ink-body);
  }
  .service-list li { position: relative; padding-left: 32px; }
  .service-list li::before {
    content: ""; position: absolute; left: 4px; top: 12px;
    width: 7px; height: 7px; border-radius: 50%;
    background: var(--accent-red);
  }
  .card-rule {
    position: absolute; left: 0; right: 0; top: 505px;
    height: 3px; background: var(--rule-grey);
  }
  .contact-bar {
    position: absolute; left: 0; right: 0; bottom: 0; height: 56px;
    background: var(--accent-red); color: var(--on-accent);
    display: flex; align-items: center; justify-content: center; gap: 16px;
    font-size: 24px;
  }
  .contact-item { display: flex; align-items: center; gap: 6px; white-space: nowrap; }
  .contact-item svg { width: 20px; height: 20px; fill: var(--on-accent); }
</style>
</head>
<body>
  <main class="business-card">
    <div class="brand">
      <div class="brand-mark"></div>
      <div class="brand-name">FLUE GUARDIAN</div>
    </div>

    <section class="service-info">
      <div class="service-headlines">
        <p>Serving VT &amp; New Hampshire since 1989</p>
        <p>Fully insured — Free estimates</p>
        <p>Family owned &amp; operated</p>
      </div>
      <ul class="service-list">
        <li>Full Masonry Services</li>
        <li>Historic chimney restoration</li>
        <li>Stainless steel liners</li>
        <li>New Chimney installations</li>
        <li>CCSA Certified Chimney sweeps</li>
      </ul>
    </section>

    <div class="card-rule"></div>

    <footer class="contact-bar">
      <span class="contact-item">
        <svg viewBox="0 0 24 24" aria-hidden="true"><path d="M6.6 10.8a15.1 15.1 0 0 0 6.6 6.6l2.2-2.2a1 1 0 0 1 1-.25 11.4 11.4 0 0 0 3.6.57 1 1 0 0 1 1 1V20a1 1 0 0 1-1 1A17 17 0 0 1 3 4a1 1 0 0 1 1-1h3.5a1 1 0 0 1 1 1c0 1.25.2 2.45.57 3.57a1 1 0 0 1-.25 1z"/></svg>
        802-555-0147
      </span>
      <span class="contact-item">
        <svg viewBox="0 0 24 24" aria-hidden="true"><path d="M3 5h18a1 1 0 0 1 1 1v12a1 1 0 0 1-1 1H3a1 1 0 0 1-1-1V6a1 1 0 0 1 1-1zm9 7 8.5-5.5h-17z"/></svg>
        info@flueguardianvt.example
      </span>
      <span class="contact-item">
        <svg viewBox="0 0 24 24" aria-hidden="true"><path d="M12 2a10 10 0 1 0 0 20 10 10 0 0 0 0-20zm-1 17.9A8 8 0 0 1 4.2 10.8L9 15.6v1a2 2 0 0 0 2 2zm6.9-2.5A2 2 0 0 0 16 16h-1v-3a1 1 0 0 0-1-1H8v-2h2a1 1 0 0 0 1-1V7h2a2 2 0 0 0 2-2v-.4a8 8 0 0 1 2.9 12.8z"/></svg>
        info@flueguardianvt.example
      </span>
    </footer>
  </main>
</body>
</html>
```